Business Card Design for Marketing Firm

Looking for business card design for higher end marketing firm. Clean but impressionable/trendy. We are a marketing firm that represents manufacturers in the foodservice equipment and supply industry. Our customers are end users such has hotels, restaurants, country clubs, convention centers and casinos as well as distributors of restaurants supplies and equipment, and manufacturers of foodservice equipment and supplies.
Target Market(s)
Hotels, Restaurants, Supply & Equipment Distributors, Foodservice Manufacturers
Industry/Entity Type
Foodservice/Hospitality
Contact Information for Business Card
Name, Title, Contact Number, Email, Website, Social Media, Address
Requirements
Must have
- Clean & Simple but Serious and Impressionable

```html
<!DOCTYPE html>
<html lang="en">
<head>
<meta charset="utf-8">
<title>Meridian Hospitality Reps – Business Card</title>
<link rel="stylesheet" href="https://fonts.googleapis.com/css2?family=Montserrat:wght@400;500;800&display=swap">
<style>
  :root {
    --backdrop: #adaeae;
    --brand-blue: #303185;
    --brand-navy: #262873;
    --paper: #ffffff;
    --ink: #1c1c2a;
  }
  * { box-sizing: border-box; margin: 0; padding: 0; }
  html, body { width: 1200px; height: 900px; overflow: hidden; }
  body {
    background: var(--backdrop);
    font-family: "Montserrat", sans-serif;
    position: relative;
  }
  .card {
    position: absolute;
    left: 285px;
    width: 630px;
    height: 360px;
    border-radius: 26px;
    overflow: hidden;
  }
  .card--back { top: 50px; background: var(--brand-blue); }
  .card--front { top: 470px; background: var(--paper); }

  /* Company name, set plainly */
  .company-name {
    position: absolute;
    font-family: "Montserrat", sans-serif;
    font-weight: 500;
    line-height: 1.3;
    white-space: nowrap;
  }

  /* Back */
  .card--back .company-name {
    left: 64px;
    top: 216px;
    font-size: 22px;
    color: var(--paper);
  }
  .social-dots { position: absolute; left: 64px; top: 290px; display: flex; gap: 6px; }
  .social-dots span { width: 13px; height: 13px; border-radius: 3px; background: var(--paper); }

  /* Front */
  .card--front .company-name {
    left: 60px;
    top: 136px;
    width: 270px;
    text-align: right;
    font-size: 17px;
    color: var(--brand-blue);
  }
  .divider {
    position: absolute; left: 358px; top: 88px; width: 1.5px; height: 140px; background: var(--brand-blue);
  }
  .contact { position: absolute; left: 378px; top: 86px; color: var(--ink); }
  .contact .person { font-weight: 800; font-size: 22px; color: var(--brand-blue); }
  .contact .title { font-size: 12px; margin-bottom: 12px; }
  .contact ul { list-style: none; }
  .contact li { display: flex; align-items: center; gap: 9px; font-size: 13px; line-height: 21px; }
  .contact svg { width: 13px; height: 13px; fill: var(--brand-blue); flex: none; }
  .address {
    position: absolute; left: 0; right: 0; bottom: 46px; text-align: center; font-size: 13px; color: var(--ink);
  }
  .bottom-band { position: absolute; left: 0; bottom: 0; width: 630px; height: 16px; }
</style>
</head>
<body>
  <section class="card card--back">
    <p class="company-name">Meridian Hospitality Reps</p>
    <div class="social-dots" aria-label="Social media"><span></span><span></span><span></span></div>
  </section>

  <section class="card card--front">
    <p class="company-name">Meridian Hospitality Reps</p>
    <div class="divider"></div>
    <div class="contact">
      <p class="person">Jonah Reyes</p>
      <p class="title">Owner</p>
      <ul>
        <li><svg viewBox="0 0 16 16"><path d="M2 6c0-2 2-3 6-3s6 1 6 3v1h-3V5.5H5V7H2zM3 8h10l1 6H2z"/></svg>(555) 214-0387</li>
        <li><svg viewBox="0 0 16 16"><path d="M4 1h8v14H4zM5.5 2.5v9h5v-9zM7 12.5h2v1H7z" fill-rule="evenodd"/></svg>(555) 214-0387</li>
        <li><svg viewBox="0 0 16 16"><path d="M1 3h14v10H1zM2 4l6 5 6-5z"/></svg>info@meridianhospitality.com</li>
        <li><svg viewBox="0 0 16 16"><circle cx="8" cy="8" r="7"/></svg>www.meridianhospitality.com</li>
      </ul>
    </div>
    <p class="address">410. 200 W. Suite 215 Cedar Falls, CO 80432</p>
    <svg class="bottom-band" viewBox="0 0 630 16" preserveAspectRatio="none">
      <polygon points="0,16 0,8 300,8 308,0 630,0 630,16" fill="var(--brand-navy)"/>
      <polygon points="296,16 304,0 312,0 304,16" fill="var(--paper)"/>
    </svg>
  </section>
</body>
</html>
```